Web and Logo Design for eCommerce site

We're launching a sister brand and require a full design for the site.

The site must have an established feel and appeal to corporate and institutional buyers.
Updates

Just a note about the wireframe design:

The Search & Rescue / Coast Guard / NVDK, etc. in the header area aren't buttons or menu items, but rather just info (along the lines of a tagline).  Sort of a "who we serve" sort of thing.

Worth noting is that it's specifically geared towards LARGE BUYERS.  For example, a police force buying 200 headlamps and 85 pairs of gloves.  So they'll register + sign in and then add a bunch of items to a RFQ.

Aim for a professional, masculine design.

Target Market(s)

We will be selling outdoor gear to the military, law enforcement, fire and rescue and first responders.

Requirements
Must have
• We require:
- Logo (vector based)

Site:
- template page
* main site template, re-skinned version of our current site
* horizontal drop-down menu
- product listings page
* thumbnail view of products
- product details page
* including elements such as product image, color/size selector, descriptions and specs (again, based loosely on our current website)
- account management page
* illustrating basic data entry styles for text box, buttons, grid, etc.

The site needs to be given a responsive design, so 2 versions of each design should be presented for desktop + mobile views.

Additional funds are available if the designer is able to fully implement the designs into a responsive framework such as bootstrap.

Nice to have
• Clean, professional design similar to:

http://military.trailvexagear.com/gov/accessories/gloves.html

http://leaf.ombrivo.com/ProductFind.aspx?language=EN&category=Hardshell&subcat=Waterproof_Jackets

```html
<!DOCTYPE html>
<html lang="en">
<head>
<meta charset="utf-8">
<title>Tundrex – Army Parka with Liner Olive</title>
<link href="https://fonts.googleapis.com/css2?family=Open+Sans:wght@400;600;700&display=swap" rel="stylesheet">
<style>
:root{
  --ink:#222;
  --muted:#555;
  --bar:#1d2630;
  --nav:#27323b;
  --olive:#6f7a3a;
  --olive-lite:#a9ae5c;
  --olive-btn:#6b6e43;
  --green:#8b9a4d;
  --red:#c8202b;
  --blue:#1d3c8c;
  --page:#d8e2e4;
  --panel:#f2f2f2;
  --footer:#16120c;
  --field:#e8e8e8;
}
*{box-sizing:border-box;margin:0;padding:0}
html,body{width:1055px;height:1200px;overflow:hidden}
body{font-family:"Open Sans",Arial,sans-serif;color:var(--ink);background:var(--page);position:relative}
.abs{position:absolute}
.topbar{left:0;top:0;width:1055px;height:30px;background:var(--bar);color:#cfd5da;font-size:9.5px}
.topbar .who{left:97px;top:9px;letter-spacing:.1px}
.topbar .who span{margin:0 7px;color:#8d959c}
.topbar .tag{right:58px;top:5px;font-size:13.5px;font-weight:600;color:#fff}
.header{left:0;top:30px;width:1055px;height:73px;background:#fff}
.brand{left:99px;top:20px;display:flex;align-items:center;gap:8px;font-size:28px;font-weight:700;color:var(--olive-btn)}
.brand i{display:block;width:22px;height:22px;background:var(--olive-btn)}
.contact{right:57px;top:28px;font-size:12px;color:#666;display:flex;align-items:center;gap:6px}
.nav{left:97px;top:104px;width:861px;height:37px;background:linear-gradient(#2f3a43,#1e2830);display:flex;align-items:center;padding-left:18px;gap:25px;font-size:12.5px;color:var(--olive-lite)}
.nav .on{color:#fff;font-weight:600}
.nav .search{position:absolute;right:12px;top:7px;width:23px;height:22px;background:var(--green)}
.panel{left:97px;top:149px;width:861px;height:727px;background:#fff}
.crumbs{left:112px;top:167px;font-size:11.5px}
.crumbs a{color:var(--ink)}
.photo{left:111px;top:203px;width:385px;height:371px;border:1px solid #ddd;background:radial-gradient(ellipse at 50% 50%,#a88a63 0,#9d7f58 38%,#fff 62%)}
.thumb{top:589px;width:57px;height:55px;border:1px solid #ddd;background:radial-gradient(#a88a63 30%,#fff 72%)}
.title{left:527px;top:196px;font-size:24px;font-weight:500}
.desc{left:527px;top:238px;width:395px;font-size:11px;line-height:17.6px;color:#444}
.more{left:527px;top:316px;font-size:10px;color:var(--olive)}
.more a{color:var(--olive)}
.price{top:350px}
.price .lab{font-size:14px}
.price .val{font-size:26px;font-weight:600;line-height:30px}
.retail{left:527px;color:var(--olive)}
.yours{left:644px;color:var(--red)}
.vline{top:350px;width:1px;height:46px;background:#ddd}
.ship{left:805px;top:352px;font-size:10.5px;line-height:17.6px}
.optbox{left:524px;width:394px;background:var(--panel)}
.optlab{position:absolute;left:16px;font-size:13px;font-weight:600}
.chip{position:absolute;height:21px;border:1px solid #bbb;background:#fff;font-size:13px;text-align:center;line-height:19px}
.chip.on{background:var(--green);color:#fff;border-color:var(--green)}
.color{height:26px;line-height:24px;font-size:12px}
.rfq{left:524px;top:614px;width:122px;height:37px;background:linear-gradient(#2a4ea4,var(--blue));color:#fff;font-weight:700;font-size:16px;text-align:center;line-height:37px;border-radius:2px}
.tab{top:709px;height:35px;font-size:14.5px;line-height:35px;text-align:center;background:var(--olive-btn);color:#fff}
.tab.on{background:#f6f6f6;color:#333;border:1px solid #ddd;border-bottom:none;height:36px;z-index:2}
.tabbody{left:112px;top:743px;width:828px;height:112px;border:1px solid #ddd;background:#f6f6f6;padding:21px 12px;font-size:11.3px;line-height:16px;color:#555}
.footer{left:0;top:899px;width:1055px;height:301px;background:var(--footer);color:#ddd}
.fh{top:41px;font-size:14.5px;font-weight:600;color:#fff}
.flist{top:78px;list-style:none;font-size:11.5px;line-height:19.4px;color:#ccc}
.ftext{left:440px;top:78px;width:240px;font-size:11px;line-height:17px;color:#bbb}
.email{left:440px;top:121px;width:148px;height:34px;background:#fff;color:#999;font-size:11.5px;padding:9px 9px}
.enter{left:608px;top:121px;width:54px;height:34px;background:#d5d5d5;color:#333;font-size:13px;text-align:center;line-height:34px}
.field{left:766px;width:194px;height:22px;background:var(--field);color:#222;font-size:10px;padding:4px 10px}
.submit{left:765px;top:220px;width:75px;height:21px;background:var(--green);color:#fff;font-size:10px;text-align:center;line-height:21px}
.copy{left:0;top:258px;width:1088px;text-align:center;font-size:11.5px;color:#fff}
</style>
</head>
<body>
<div class="abs topbar">
  <div class="abs who">SEARCH &amp; RESCUE<span>|</span>COAST GUARD<span>|</span>FIREFIGHTERS<span>|</span>MILITARY<span>|</span>LAW ENFORCEMENT<span>|</span>NVDK</div>
  <div class="abs tag">Serving those who serve</div>
</div>
<div class="abs header">
  <div class="abs brand"><i></i>Tundrex</div>
  <div class="abs contact">
    <svg width="15" height="15" viewBox="0 0 16 16"><path d="M3 1l3 3-1.5 2c1 2 3 4 5 5l2-1.5 3 3-2 2C6 14 2 10 1 3z" fill="#888"/></svg>
    Call (+) 0800.555.019
    <svg width="17" height="14" viewBox="0 0 18 14" style="margin-left:8px"><path d="M1 4h16l-2 9H3z M5 4l3-3 M13 4l-3-3" fill="none" stroke="#888" stroke-width="1.5"/></svg>
    (0 item) - $0.00 &nbsp;▾
  </div>
</div>
<nav class="abs nav">
  <span class="on">RESCUE GEAR</span><span>FOOTWEAR</span><span>CLOTHING</span><span>TENTS MATS SLEEPING BAGS</span><span>CAMPING GEAR</span><span>SNOW SPORTS</span><span>BRAND'S</span>
  <span class="search"><svg width="23" height="22" viewBox="0 0 23 22"><circle cx="10" cy="10" r="4.5" fill="none" stroke="#fff" stroke-width="2"/><path d="M13.5 13.5l4 4" stroke="#fff" stroke-width="2"/></svg></span>
</nav>
<div class="abs panel"></div>
<div class="abs crumbs"><a href="#">Rescue Gear</a> &nbsp;&gt;&nbsp; <a href="#">Helmet</a> &nbsp;&gt;&nbsp; <a href="#">Maze Helmet</a></div>
<div class="abs photo" role="img" aria-label="Product photo: olive army parka shirt, front view"></div>
<svg class="abs" style="left:171px;top:609px" width="9" height="13"><path d="M8 0v13L0 6.5z" fill="var(--olive)"/></svg>
<div class="abs thumb" style="left:201px" role="img" aria-label="Parka thumbnail 1"></div>
<div class="abs thumb" style="left:265px" role="img" aria-label="Parka thumbnail 2"></div>
<div class="abs thumb" style="left:330px" role="img" aria-label="Parka thumbnail 3"></div>
<svg class="abs" style="left:406px;top:609px" width="9" height="13"><path d="M1 0v13l8-6.5z" fill="var(--olive)"/></svg>

<h1 class="abs title">Army Parka with Liner Olive</h1>
<p class="abs desc">All the actual measurements given on the site as "armpit to armpit x 2" refer to the measurements of the garment and not the size it will fit.<br>The best way of checking if an item will fit is to measure a similar garment you have which fits well and compare the measurements.</p>
<div class="abs more">+ <a href="#">more</a></div>
<div class="abs price retail"><div class="lab">RETAIL PRICE</div><div class="val">$199.99</div></div>
<div class="abs vline" style="left:629px"></div>
<div class="abs price yours"><div class="lab">YOUR PRICE LEVEL</div><div class="val">$150.99</div></div>
<div class="abs vline" style="left:786px"></div>
<div class="abs ship">Free Canada Shipping<br>In Stock<br>Ship in 24 hours</div>

<div class="abs optbox" style="top:419px;height:82px">
  <span class="optlab" style="top:33px">SIZES:</span>
  <span class="chip on" style="left:105px;top:18px;width:25px">8</span>
  <span class="chip" style="left:137px;top:18px;width:25px">8.5</span>
  <span class="chip" style="left:168px;top:18px;width:24px">9</span>
  <span class="chip" style="left:199px;top:18px;width:25px">9.5</span>
  <span class="chip" style="left:230px;top:18px;width:24px">10</span>
  <span class="chip" style="left:260px;top:18px;width:33px">10.5</span>
  <span class="chip" style="left:299px;top:18px;width:24px">11</span>
  <span class="chip" style="left:330px;top:18px;width:33px">11.5</span>
  <span class="chip" style="left:105px;top:47px;width:24px">12</span>
  <span class="chip" style="left:137px;top:47px;width:33px">12.5</span>
  <span class="chip" style="left:176px;top:47px;width:24px">13</span>
  <span class="chip" style="left:207px;top:47px;width:33px">13.5</span>
</div>
<div class="abs optbox" style="top:504px;height:41px">
  <span class="optlab" style="left:10px;top:11px">COLORS:</span>
  <span class="chip color" style="left:104px;top:7px;width:43px">Black</span>
  <span class="chip color" style="left:151px;top:7px;width:52px">Orange</span>
  <span class="chip color" style="left:208px;top:7px;width:52px">Green</span>
  <span class="chip color" style="left:265px;top:7px;width:52px">Yellow</span>
</div>
<div class="abs optbox" style="top:549px;height:42px">
  <span class="optlab" style="left:10px;top:13px">QUANTITY:</span>
  <span class="chip" style="left:104px;top:6px;width:42px;height:29px;line-height:27px;font-size:11px">1</span>
</div>
<div class="abs rfq">ADD TO RFQ</div>

<div class="abs tab on" style="left:124px;width:107px">Overview</div>
<div class="abs tab" style="left:243px;width:89px">Specs</div>
<div class="abs tab" style="left:342px;width:151px">Extended Specs</div>
<div class="abs tabbody">It is a long established fact that a reader will be distracted by the readable content of a page when looking at its layout. The point of using Lorem Ipsum is that it has a more-or-less normal distribution of letters, as opposed to using 'Content here, content here', making it look like readable English. Many desktop publishing packages and web page editors now use Lorem Ipsum as their default model text, and a search for 'lorem ipsum' will uncover many web sites still in their infancy. Various versions have evolved over the years, sometimes by accident, sometimes on purpose (injected humour and the like).</div>

<footer class="abs footer">
  <div class="abs fh" style="left:102px">Navigation</div>
  <ul class="abs flist" style="left:102px"><li>Rescue Gear</li><li>Footwear</li><li>Clothing</li><li>Tents Mats</li><li>Sleeping Bags</li><li>Camping Gear</li><li>Snow Sports</li><li>Brands</li></ul>
  <div class="abs fh" style="left:277px">Products</div>
  <ul class="abs flist" style="left:277px"><li>Rescue Gear</li><li>Footwear</li><li>Clothing</li><li>Tents Mats</li><li>Sleeping Bags</li><li>Camping Gear</li><li>Snow Sports</li><li>Brands</li></ul>
  <div class="abs fh" style="left:440px">Get informed for our Special offers</div>
  <p class="abs ftext">Get the best and most interesting discount offers via email.</p>
  <div class="abs email">you@example.com</div>
  <div class="abs enter">Enter</div>
  <div class="abs fh" style="left:766px">Quick Contact</div>
  <div class="abs field" style="top:67px">Name:</div>
  <div class="abs field" style="top:95px">Email:</div>
  <div class="abs field" style="top:123px">Phone:</div>
  <div class="abs field" style="top:152px;height:59px;padding-top:7px">Message:</div>
  <div class="abs submit">SUMBIT</div>
  <div class="abs copy">CopyRight © 2014 TUNDREX All Received</div>
</footer>
</body>
</html>
```